redesign of my existing custom website into Wordpress based website

I need someone to redesign my current website into something more classy, simplistic, modern and on trend. I would like it set up on Wordpress in a way thats easy for me to make my own additions to blogs/price changes and promotion banners. I will also need a page that is password protected so members can login and have access to all my training videos and resources.
website is www.tidewellmamas.com.au

Target Market(s)

new mums

Industry/Entity Type

Fitness

Coding

Coded - Design and coding required

Number of Pages Required

5+ page

Colors
33a6d7

Requirements
Must have
• chic, modern, stylish and simplistic.
• a call to action above the page fold
• mobile friendly conversion
• a pop up message as soon as someone enters my sight offering my free report
• a members page that is password protected containing 3 youtube videos and 6 pdf attachments as resources
• a home page
• a contact us page
• an about us page
• a blog page
• a store page
Nice to have
• some examples of my peers websites that I like:
• www.norapellwick.com
• https://www.9qlr.com
• https://41bytedgarth.com
Should not have
• anything gimmicky

```html
<!DOCTYPE html>
<html lang="en">
<head>
<meta charset="utf-8">
<title>Tidewell Mamas – 12 Week Home Workout Program For Mums</title>
<link rel="stylesheet" href="https://fonts.googleapis.com/css2?family=Dancing+Script:wght@500;700&family=Open+Sans:wght@400;600;700&family=Oswald:wght@400;500&display=swap">
<style>
:root{
  --pink:#e5087e;
  --pink-dark:#c8046c;
  --blue:#33a6d7;
  --blue-deep:#2b93c4;
  --ink:#333;
  --muted:#777;
  --line:#e4e4e4;
  --paper:#fff;
  --footer:#f1f1f1;
  --lilac:#b99acb;
}
*{box-sizing:border-box;margin:0;padding:0}
html,body{width:1200px;height:4265px;overflow:hidden}
body{font-family:"Open Sans",Arial,sans-serif;color:var(--ink);background:var(--paper);position:relative}
section,header,footer{position:absolute;left:0;width:1200px}
.abs{position:absolute}
.script{font-family:"Dancing Script",cursive;font-weight:700}
.center{text-align:center}
.intro{position:absolute;left:270px;width:660px;text-align:center;font-size:11px;line-height:26px;color:#666}
.btn{position:absolute;display:block;color:#fff;font-size:12px;font-weight:700;text-transform:uppercase;text-align:center;line-height:34px;height:34px;border-radius:3px}
.btn.pink{background:var(--pink)}
.btn.blue{background:var(--blue)}

/* header */
.site-header{top:0;height:100px;background:var(--paper);border-top:4px solid var(--blue)}
.brand{left:85px;top:22px;display:flex;align-items:center;gap:10px}
.brand-dot{width:46px;height:46px;border-radius:50%;background:var(--pink)}
.brand-name{font-family:"Dancing Script",cursive;font-weight:700;font-size:26px;color:var(--pink)}
.nav{left:448px;top:36px;display:flex;gap:50px;font-size:13px;font-weight:600;text-transform:uppercase;color:#444}
.nav-icon{top:28px;width:40px;height:40px;border-radius:50%;border:2px solid;display:flex;align-items:center;justify-content:center}

/* hero */
.hero{top:100px;height:548px;overflow:hidden}
.hero-photo{left:0;top:0;width:1200px;height:548px;background:linear-gradient(90deg,#f4f2f1 0%,#ecebe8 35%,#d8d3cc 55%,#cfc4b5 75%,#e3ddd4 100%)}
.hero-band{left:0;bottom:0;width:1200px;height:36px;background:linear-gradient(90deg,#cdb7d8,var(--lilac))}
.hero-title{left:85px;top:108px;font-size:60px;color:var(--pink);font-weight:600}
.hero-sub{left:85px;top:180px;font-size:30px;color:var(--blue)}
.hero-list{left:85px;top:232px;list-style:none;font-size:13px;color:#444}
.hero-list li{height:30px;display:flex;align-items:center;gap:14px}
.hero-dots{left:85px;top:502px;display:flex;gap:6px}
.hero-dots span{width:14px;height:14px;border-radius:50%;border:2px solid var(--pink);background:#fff}
.hero-dots span.on{background:var(--pink)}

/* titles */
.sec-title{position:absolute;left:0;width:1200px;text-align:center;font-family:"Dancing Script",cursive;font-weight:700;font-size:40px;color:var(--pink)}

/* welcome */
.welcome{top:648px;height:688px;background:var(--paper)}
.card{position:absolute;width:330px;background:#fff;box-shadow:0 1px 4px rgba(0,0,0,.15)}
.card-photo{position:absolute;left:0;top:0;width:330px}
.feature .card-photo{height:165px}
.feature-icon{position:absolute;left:20px;top:125px;width:76px;height:76px;border-radius:50%;display:flex;align-items:center;justify-content:center}
.card-title{position:absolute;left:20px;font-size:14px;font-weight:700;text-transform:uppercase;color:#333}
.card-text{position:absolute;left:20px;width:290px;font-size:11px;line-height:20px;color:#777}

/* trial */
.trial{top:1336px;height:796px;background:linear-gradient(180deg,var(--blue) 0%,#3aa9da 50%,var(--blue-deep) 100%)}
.trial .sec-title{color:#fff;top:36px}
.trial-sub{position:absolute;left:0;width:1200px;top:96px;text-align:center;font-family:"Dancing Script",cursive;font-size:26px;color:#fff;font-weight:600}
.offer{position:absolute;left:364px;top:157px;width:475px;height:560px;background:#fff}
.offer-top{position:absolute;left:0;top:0;width:475px;height:330px;background:#f6f6f6}
.offer-get{left:24px;top:22px;font-family:"Oswald",sans-serif;font-size:44px;color:#555;line-height:1}
.offer-free{left:24px;top:76px;font-family:"Oswald",sans-serif;font-size:46px;color:var(--blue);line-height:1}
.offer-tips{left:24px;top:138px;z-index:2;white-space:nowrap;font-family:"Dancing Script",cursive;font-weight:700;font-size:24px;color:var(--pink)}
.offer-note{left:24px;top:190px;width:210px;font-size:11px;font-style:italic;line-height:18px;color:#555}
.offer-tag{left:40px;top:270px;background:var(--pink);color:#fff;font-family:"Dancing Script",cursive;font-weight:700;font-size:18px;padding:6px 14px;transform:rotate(-12deg)}
.offer-photo{left:285px;top:15px;width:180px;height:315px;z-index:1;background:linear-gradient(180deg,#eeeeee,#d9e8c5 55%,#c7e08c 80%,#e8e8e8)}
.field-label{position:absolute;left:24px;font-size:14px;color:#444}
.field{position:absolute;left:24px;width:425px;height:36px;border:1px solid #ccc;border-radius:3px;background:#fff}
.submit{position:absolute;left:346px;top:517px;width:86px;height:86px;border-radius:50%;background:var(--pink);color:#fff;font-size:12px;font-weight:700;display:flex;align-items:center;justify-content:center}

/* results */
.results{top:2132px;height:668px;background:var(--paper)}
.result .card-photo{height:270px;display:flex}
.result .card-photo div{flex:1}
.price-badge{position:absolute;left:135px;top:238px;width:60px;height:60px;border-radius:50%;background:var(--pink);color:#fff;font-weight:700;font-size:16px;display:flex;align-items:center;justify-content:center}
.result .card-title{left:0;width:330px;text-align:center}
.result-sub{position:absolute;left:0;width:330px;text-align:center;font-size:14px;color:var(--pink)}

/* pricing */
.pricing{top:2800px;height:549px;background:var(--pink)}
.pricing .sec-title{color:#fff;top:38px}
.pricing .intro{color:#fff;top:94px}
.plan{position:absolute;top:190px;width:490px;color:#fff}
.plan-price{font-size:62px;font-weight:600;line-height:1}
.plan-price small{font-size:28px;font-weight:400}
.plan-lead{margin-top:18px;font-size:12px;font-weight:700;line-height:20px;width:430px}
.plan-list{list-style:none;margin-top:16px;font-size:12px}
.plan-list li{height:30px;display:flex;align-items:center;gap:12px}
.plan-pack{position:absolute;top:150px;width:180px;height:180px;border-radius:50%;border:5px solid #fff}

/* blog */
.blog{top:3349px;height:588px;background:var(--paper)}
.post{position:absolute;top:156px;width:330px}
.post-photo{width:330px;height:208px}
.post-title{margin-top:26px;font-size:14px;font-weight:700;text-transform:uppercase}
.post-meta{margin-top:12px;display:flex;gap:34px;font-size:10px;color:#999}
.post-text{margin-top:18px;font-size:11px;line-height:20px;color:#777}

/* footer */
.site-footer{top:3937px;height:271px;background:var(--footer)}
.foot-col{position:absolute;top:40px}
.foot-col h4{font-size:16px;font-weight:700;color:#333;margin-bottom:14px}
.foot-col ul{list-style:none;font-size:11px;color:#555;line-height:27px}
.sub-input{position:absolute;left:0;top:66px;width:228px;height:38px;background:#fff;border:1px solid #ddd;font-size:11px;color:#999;padding:11px 10px}
.sub-btn{position:absolute;left:228px;top:66px;width:98px;height:38px;background:var(--blue);color:#fff;font-size:11px;font-weight:700;text-align:center;line-height:38px}
.socials{position:absolute;left:0;top:191px;display:flex;gap:6px}
.socials span{width:32px;height:32px;border-radius:50%;background:#9aa3a8}
.copyright{top:4208px;height:57px;background:#fff;text-align:center;font-size:11px;color:#777;line-height:57px}
</style>
</head>
<body>

<header class="site-header">
  <div class="abs brand"><span class="brand-dot"></span><span class="brand-name">Tidewell Mamas</span></div>
  <nav class="abs nav"><span>Home</span><span>About Us</span><span>Program</span><span>Blog</span><span>Shop</span><span>Contact Us</span></nav>
  <div class="abs nav-icon" style="left:1028px;border-color:var(--pink)">
    <svg width="18" height="16" viewBox="0 0 18 16"><path d="M1 2h3l2 8h9l2-6H5" fill="none" stroke="#e5087e" stroke-width="2"/><circle cx="7" cy="13.5" r="1.6" fill="#e5087e"/><circle cx="14" cy="13.5" r="1.6" fill="#e5087e"/></svg>
  </div>
  <div class="abs nav-icon" style="left:1080px;border-color:var(--blue)">
    <svg width="16" height="16" viewBox="0 0 16 16"><circle cx="6.5" cy="6.5" r="5" fill="none" stroke="#33a6d7" stroke-width="2"/><path d="M10.5 10.5L15 15" stroke="#33a6d7" stroke-width="2"/></svg>
  </div>
</header>

<section class="hero">
  <div class="abs hero-photo" role="img" aria-label="Mother kneeling on a living room floor with a light dumbbell while her toddler reaches for it"></div>
  <div class="abs hero-band"></div>
  <h1 class="abs hero-title script">Tidewell Mamas</h1>
  <p class="abs hero-sub script">12 week Home Workout Program For Mums!</p>
  <ul class="abs hero-list">
    <li><svg width="12" height="10" viewBox="0 0 12 10"><path d="M1 5l3.5 3.5L11 1" fill="none" stroke="#444" stroke-width="2"/></svg>12 week, cardio and resistance circuit training program</li>
    <li><svg width="12" height="10" viewBox="0 0 12 10"><path d="M1 5l3.5 3.5L11 1" fill="none" stroke="#444" stroke-width="2"/></svg>Triple workout DVD</li>
    <li><svg width="12" height="10" viewBox="0 0 12 10"><path d="M1 5l3.5 3.5L11 1" fill="none" stroke="#444" stroke-width="2"/></svg>Workout equipment delivered to your front door</li>
    <li><svg width="12" height="10" viewBox="0 0 12 10"><path d="M1 5l3.5 3.5L11 1" fill="none" stroke="#444" stroke-width="2"/></svg>Weekly coaching emails</li>
    <li><svg width="12" height="10" viewBox="0 0 12 10"><path d="M1 5l3.5 3.5L11 1" fill="none" stroke="#444" stroke-width="2"/></svg>Accountability charts &amp; program cards</li>
  </ul>
  <a class="btn pink" style="left:85px;top:410px;width:155px">Read More Info</a>
  <div class="abs hero-dots"><span></span><span class="on"></span><span></span></div>
</section>

<section class="welcome">
  <h2 class="sec-title" style="top:48px">Welcome to Tidewell Mamas</h2>
  <p class="intro" style="top:104px">Spending a lot of time researching the best post pregnancy training methods, I created this program to help me get back into shape after my second baby. In just 12 weeks using this program I was back to my pre-baby.</p>

  <article class="card feature" style="left:85px;top:182px;height:455px">
    <div class="card-photo" role="img" aria-label="Mum training with a resistance band at home" style="background:linear-gradient(135deg,#3a3a3a,#7a5a66 50%,#c94d8f)"></div>
    <div class="feature-icon" style="background:var(--pink)"><svg width="34" height="34" viewBox="0 0 34 34"><circle cx="17" cy="8" r="5" fill="#fff"/><path d="M9 32V20q0-6 8-6t8 6v12z" fill="#fff"/></svg></div>
    <h3 class="card-title" style="top:222px">Specially Designed for Mums</h3>
    <p class="card-text" style="top:250px">Unlike other home workout programs out there ours is designed specially for mums. Because our bodies go such a major change during pregnancy.</p>
    <a class="btn pink" style="left:20px;top:390px;width:90px;height:30px;line-height:30px;font-size:10px">Read More</a>
  </article>

  <article class="card feature" style="left:435px;top:182px;height:455px">
    <div class="card-photo" role="img" aria-label="Mum doing push-ups on a mat beside her baby" style="background:linear-gradient(135deg,#4a4040,#8c6f6a 50%,#c45aa0)"></div>
    <div class="feature-icon" style="background:var(--blue)"><svg width="32" height="34" viewBox="0 0 32 34"><path d="M16 10c-4-3-13-2-13 8s7 15 10 14c2-1 4-1 6 0 3 1 10-4 10-14s-9-11-13-8z" fill="#fff"/><path d="M16 10c0-4 2-7 6-8" fill="none" stroke="#fff" stroke-width="2"/></svg></div>
    <h3 class="card-title" style="top:222px">Workout Equipment Included</h3>
    <p class="card-text" style="top:250px">Unlike other home workout programs out there ours is designed specially for mums. Because our bodies go such a major change during pregnancy.</p>
    <a class="btn blue" style="left:20px;top:390px;width:90px;height:30px;line-height:30px;font-size:10px">Read More</a>
  </article>

  <article class="card feature" style="left:785px;top:182px;height:455px">
    <div class="card-photo" role="img" aria-label="Mum lifting a red dumbbell in her lounge room" style="background:linear-gradient(135deg,#2f2f2f,#6b5050 50%,#b33a3a)"></div>
    <div class="feature-icon" style="background:var(--pink)"><svg width="32" height="34" viewBox="0 0 32 34"><circle cx="16" cy="19" r="12" fill="none" stroke="#fff" stroke-width="3"/><path d="M16 19V12M12 3h8" stroke="#fff" stroke-width="3"/></svg></div>
    <h3 class="card-title" style="top:222px">Post Baby Recovery</h3>
    <p class="card-text" style="top:250px">Unlike other home workout programs out there ours is designed specially for mums. Because our bodies go such a major change during pregnancy.</p>
    <a class="btn pink" style="left:20px;top:390px;width:90px;height:30px;line-height:30px;font-size:10px">Read More</a>
  </article>
</section>

<section class="trial">
  <h2 class="sec-title">Free Trial Today!</h2>
  <p class="trial-sub">Start Creating your best body ever today!</p>
  <form class="offer">
    <div class="offer-top">
      <p class="abs offer-get">GET YOUR</p>
      <p class="abs offer-free">FREE TOP 10</p>
      <p class="abs offer-tips">Baby Belly Blasting Tips</p>
      <p class="abs offer-note">See our secret tips to a flatter yummy mummy tummy that you can start implementing</p>
      <p class="abs offer-tag">For Free Today!</p>
      <div class="abs offer-photo" role="img" aria-label="Trainer standing in a lime green workout top"></div>
    </div>
    <label class="field-label" style="top:355px">Name :</label>
    <div class="field" style="top:378px"></div>
    <label class="field-label" style="top:438px">Email :</label>
    <div class="field" style="top:458px"></div>
    <div class="submit">SUBMIT</div>
  </form>
</section>

<section class="results">
  <h2 class="sec-title" style="top:36px">Before &amp; After</h2>
  <p class="intro" style="top:90px">Spending a lot of time researching the best post pregnancy training methods, I created this program to help me get back into shape after my second baby. In just 12 weeks using this program I was back to my pre-baby.</p>

  <article class="card result" style="left:85px;top:165px;height:455px">
    <div class="card-photo" role="img" aria-label="Before and after photos of a mum in white underwear"><div style="background:linear-gradient(180deg,#f3eeea,#e8d7cc)"></div><div style="background:linear-gradient(180deg,#f1ece8,#e6d4c8)"></div></div>
    <div class="price-badge">$29</div>
    <h3 class="card-title" style="top:310px">Marisol</h3>
    <p class="result-sub" style="top:334px">Lost 17 kgs and 25 cms in 12 weeks!</p>
    <p class="card-text" style="top:366px">The 12 week Little Belly Reset was fantastic! I really enjoyed the different workouts, they started at just the right level and progressed</p>
  </article>

  <article class="card result" style="left:435px;top:165px;height:455px">
    <div class="card-photo" role="img" aria-label="Before and after photos of a mum in a black top and jeans"><div style="background:linear-gradient(180deg,#f2f2f2,#c9cfd8)"></div><div style="background:linear-gradient(180deg,#f2f2f2,#bcc6d4)"></div></div>
    <div class="price-badge">$29</div>
    <h3 class="card-title" style="top:310px">Pippa</h3>
    <p class="result-sub" style="top:334px">Lost 31 cms and 10kgs in 8 weeks!</p>
    <p class="card-text" style="top:366px">The 12 week Little Belly Reset was fantastic! I really enjoyed the different workouts, they started at just the right level and progressed</p>
  </article>

  <article class="card result" style="left:785px;top:165px;height:455px">
    <div class="card-photo" role="img" aria-label="Before and after photos of a mum in white underwear"><div style="background:linear-gradient(180deg,#f4f1ee,#e9d9cf)"></div><div style="background:linear-gradient(180deg,#f4f1ee,#e6d8cf)"></div></div>
    <div class="price-badge">$29</div>
    <h3 class="card-title" style="top:310px">Yvette</h3>
    <p class="result-sub" style="top:334px">Lost 20 cms in 12 weeks!</p>
    <p class="card-text" style="top:366px">The 12 week Little Belly Reset was fantastic! I really enjoyed the different workouts, they started at just the right level and progressed</p>
  </article>
</section>

<section class="pricing">
  <h2 class="sec-title">12 Week Home Workout Program For Mums!</h2>
  <p class="intro">Spending a lot of time researching the best post pregnancy training methods, I created this program to help me get back into shape after my second baby. In just 12 weeks using this program I was back to my pre-baby.</p>

  <div class="plan" style="left:85px">
    <p class="plan-price">$89<small> / Only $7.50 per week!</small></p>
    <p class="plan-lead">Spending a lot of time researching the best post pregnancy training methods, I created this program to help me get back into second baby.</p>
    <ul class="plan-list">
      <li><svg width="12" height="10" viewBox="0 0 12 10"><path d="M1 5l3.5 3.5L11 1" fill="none" stroke="#fff" stroke-width="2"/></svg>Our 3 stage, 12 week training program</li>
      <li><svg width="12" height="10" viewBox="0 0 12 10"><path d="M1 5l3.5 3.5L11 1" fill="none" stroke="#fff" stroke-width="2"/></svg>Full Instructional Workout DVD</li>
      <li><svg width="12" height="10" viewBox="0 0 12 10"><path d="M1 5l3.5 3.5L11 1" fill="none" stroke="#fff" stroke-width="2"/></svg>Weekly accountability charts</li>
      <li><svg width="12" height="10" viewBox="0 0 12 10"><path d="M1 5l3.5 3.5L11 1" fill="none" stroke="#fff" stroke-width="2"/></svg>Weekly Coaching emails</li>
      <li><svg width="12" height="10" viewBox="0 0 12 10"><path d="M1 5l3.5 3.5L11 1" fill="none" stroke="#fff" stroke-width="2"/></svg>Nutritionist approved Healthy</li>
    </ul>
    <div class="plan-pack" role="img" aria-label="Program booklets and cards" style="left:290px;background:radial-gradient(circle,#fff 30%,#f3d6e6 70%,#e7b3cf)"></div>
  </div>

  <div class="plan" style="left:630px">
    <p class="plan-price">$199<small> / Only $16.60 per week!</small></p>
    <p class="plan-lead">Spending a lot of time researching the best post pregnancy training methods, I created this program to help me get back into second baby.</p>
    <ul class="plan-list">
      <li><svg width="12" height="10" viewBox="0 0 12 10"><path d="M1 5l3.5 3.5L11 1" fill="none" stroke="#fff" stroke-width="2"/></svg>Our 3 stage, 12 week training program</li>
      <li><svg width="12" height="10" viewBox="0 0 12 10"><path d="M1 5l3.5 3.5L11 1" fill="none" stroke="#fff" stroke-width="2"/></svg>Full Instructional Workout</li>
      <li><svg width="12" height="10" viewBox="0 0 12 10"><path d="M1 5l3.5 3.5L11 1" fill="none" stroke="#fff" stroke-width="2"/></svg>Weekly accountability charts</li>
      <li><svg width="12" height="10" viewBox="0 0 12 10"><path d="M1 5l3.5 3.5L11 1" fill="none" stroke="#fff" stroke-width="2"/></svg>Weekly Coaching emails</li>
      <li><svg width="12" height="10" viewBox="0 0 12 10"><path d="M1 5l3.5 3.5L11 1" fill="none" stroke="#fff" stroke-width="2"/></svg>Nutritionist approved Healthy</li>
    </ul>
    <div class="plan-pack" role="img" aria-label="Full program pack with DVD, booklets and workout equipment" style="left:295px;background:radial-gradient(circle,#fff 25%,#d9d0dc 60%,#8a6f8f)"></div>
  </div>
</section>

<section class="blog">
  <h2 class="sec-title" style="top:28px">Latest Blog</h2>
  <p class="intro" style="top:84px">Spending a lot of time researching the best post pregnancy training methods, I created this program to help me get back into second baby. In just 12 weeks using this program I was back to my pre-baby.</p>

  <article class="post" style="left:85px">
    <div class="post-photo" role="img" aria-label="Mum holding her baby close after a workout" style="background:linear-gradient(135deg,#3a2e2a,#9a6f5a 55%,#d3a98c)"></div>
    <h3 class="post-title">The Benefits of Training</h3>
    <p class="post-meta"><span>27 March 2016</span><span>130</span><span>Like</span><span>Share</span></p>
    <p class="post-text">Spending a lot of time researching the best post pregnancy training methods, I created this program help me get back into second baby. In just 12 weeks</p>
  </article>
  <article class="post" style="left:435px">
    <div class="post-photo" role="img" aria-label="Mum stretching on a rug in her living room" style="background:linear-gradient(135deg,#5a4a40,#8e7c6c 55%,#b9a792)"></div>
    <h3 class="post-title">Creamy Pumpkin Soup</h3>
    <p class="post-meta"><span>27 March 2016</span><span>130</span><span>Like</span><span>Share</span></p>
    <p class="post-text">Spending a lot of time researching the best post pregnancy training methods, I created this program help me get back into second baby. In just 12 weeks</p>
  </article>
  <article class="post" style="left:785px">
    <div class="post-photo" role="img" aria-label="Mum exercising on a mat next to her toddler" style="background:linear-gradient(135deg,#4a3f3f,#8a6f78 55%,#c7b0bf)"></div>
    <h3 class="post-title">Healthy Shepherds Pie Recipe</h3>
    <p class="post-meta"><span>27 March 2016</span><span>130</span><span>Like</span><span>Share</span></p>
    <p class="post-text">Spending a lot of time researching the best post pregnancy training methods, I created this program help me get back into second baby. In just 12 weeks</p>
  </article>
</section>

<footer class="site-footer">
  <div class="foot-col" style="left:102px"><h4>Quick Links</h4><ul><li>Home</li><li>About Us</li><li>Programs</li><li>Blog</li><li>Shop</li><li>Contact</li></ul></div>
  <div class="foot-col" style="left:284px"><h4>Help &amp; support</h4><ul><li>Recommended Reading</li><li>Submit your Story</li><li>Contact Us</li><li>Frequently Asked Questions</li><li>How to Order</li></ul></div>
  <div class="foot-col" style="left:532px"><h4>My Account</h4><ul><li>Customer Support</li><li>My Account</li><li>Order Tracking</li><li>Reminder Service</li><li>Returns &amp; Files</li></ul></div>
  <div class="foot-col" style="left:782px;width:330px">
    <h4>Email Subscription</h4>
    <ul><li>Register your email address to get information about us</li></ul>
    <div class="sub-input">Email Address</div>
    <div class="sub-btn">SUBSCRIBE</div>
    <h4 style="position:absolute;top:150px;white-space:nowrap">Stay Connected</h4>
    <div class="socials"><span></span><span></span><span></span><span></span><span></span><span></span><span></span><span></span><span></span></div>
  </div>
</footer>

<div class="abs copyright" style="left:0;width:1200px">Copyright © 2016, Tidewell Mamas, All Rights Reserved &nbsp;|&nbsp; Privacy Policy &nbsp;|&nbsp; Terms of Use &nbsp;|&nbsp; Feedback</div>

</body>
</html>
```